Open Harbor book needs a cover design

I need a front and back cover design that demonstrates a strong sense of possibility that trust can be repaired even if things look bleak. Repairing trust is difficult, but this book is full of wisdom, proven strategies, and doctoral research to help people strengthen relationships and improve trust. It can help any group: business, nonprofit, education, service. Showing diversity of groups and people is very important. For the cover title, there should be a play on words: "Open Harbor: Is it? Within Reach" should have the words "is it?" crossed out and the words "It IS! should be replaced there in a striking way. Perhaps in red ink. For publishing purposes, book will be titled Open Harbor: It IS Within Reach! Please see the attachment for an example. The book layout is approximately 260 pages.

A business self-help book, but the target is any person in a group that feels they have lost trust in each other. It can be just a normal person struggling in a volunteer group they are a part of, or a supervisor whose group is not working well together. It can be a leader who just wants their group to be stronger.

Business Management

• Allise - I believe is being used on the interior of the book for the title page and headings

• Show hope and possibility in the midst of difficulty. Must have a play on the words in the title "Open Harbor: Is it? Within Reach" with crossing out "is it?" with "It IS!" (see attached example) Must include the author's name: Marla Quentin, PhD Must include a smaller tagline: "Practical Steps to Move Teams Forward Again"
• Showing diverse people, or hands. Diverse kinds of groups - not just business. A colorful cover. Maybe show the complexity of trust when it is broken...broken pieces of trust that are then picked up and put together when people work together. Could show people (or images of hands) or other ways to show that it's a choice and it is possible to repair broken trust. I'd also like to convey a sense of a group - not just random people. That they have something at stake to work on repairing trust together and this book can help them.
• If images of people are used, just showing one gender or race is not okay. Nor just binary choices: like an image containing one man and one woman, or one white person and one person of color - otherwise it seems that the book on Open Harbor is about race or gender relations.

```html
<!DOCTYPE html>
<html lang="en">
<head>
<meta charset="utf-8">
<title>Open Harbor — Book Cover</title>
<link rel="stylesheet" href="https://fonts.googleapis.com/css2?family=Bodoni+Moda:wght@600;700&family=Cinzel:wght@400&family=Cormorant+Garamond:wght@500&family=Montserrat:wght@600&display=swap">
<style>
  :root {
    --stage: #262626;
    --ink-deep: #15124a;
    --ink-mid: #2a1f6e;
    --violet: #5a2f96;
    --orchid: #a765cf;
    --paper: #ffffff;
    --strike-red: #d8262b;
  }
  * { margin: 0; padding: 0; box-sizing: border-box; }
  html, body {
    width: 1200px;
    height: 905px;
    overflow: hidden;
    background: var(--stage);
  }
  .cover {
    position: absolute;
    left: 315px;
    top: 22px;
    width: 570px;
    height: 860px;
    overflow: hidden;
    background:
      linear-gradient(158deg, transparent 0 62%, rgba(167,101,207,0.55) 62% 72%, rgba(196,130,225,0.75) 72% 100%),
      linear-gradient(205deg, transparent 0 55%, rgba(90,47,150,0.6) 70%, transparent 85%),
      linear-gradient(170deg, var(--ink-deep) 0%, var(--ink-mid) 40%, var(--violet) 75%, var(--orchid) 100%);
    color: var(--paper);
  }
  .cover__author {
    position: absolute;
    top: 34px;
    left: 0;
    width: 100%;
    text-align: center;
    font-family: "Cinzel", serif;
    font-size: 27px;
    letter-spacing: 0.16em;
  }
  .cover__title {
    position: absolute;
    left: 0;
    top: 0;
    width: 570px;
    height: 520px;
  }
  .title-word {
    font-family: "Bodoni Moda", serif;
    font-weight: 700;
    fill: var(--paper);
  }
  .title-small {
    font-family: "Bodoni Moda", serif;
    font-weight: 700;
    fill: var(--paper);
  }
  .title-struck { fill: var(--paper); opacity: 0.9; }
  .strike { stroke: var(--strike-red); stroke-width: 4; stroke-linecap: round; fill: none; }
  .cover__tagline {
    position: absolute;
    top: 466px;
    left: 0;
    width: 100%;
    text-align: center;
    font-family: "Cormorant Garamond", serif;
    font-weight: 500;
    font-size: 19px;
    line-height: 1.05;
    text-transform: uppercase;
    letter-spacing: 0.02em;
  }
  .cover__artwork {
    position: absolute;
    left: 118px;
    top: 530px;
    width: 292px;
    height: 228px;
    background: linear-gradient(135deg, #ffffff 0%, #e9e3f4 55%, #cdbde6 100%);
  }
  .cover__publisher {
    position: absolute;
    left: 210px;
    top: 788px;
    display: flex;
    align-items: center;
    gap: 6px;
    font-family: "Montserrat", sans-serif;
    font-weight: 600;
    font-size: 11px;
    line-height: 1.05;
    color: var(--paper);
    text-transform: uppercase;
  }
  .publisher-square {
    width: 18px;
    height: 18px;
    background: var(--paper);
  }
</style>
</head>
<body>
  <main class="cover">
    <p class="cover__author">Marla Quentin, PhD</p>

    <svg class="cover__title" viewBox="0 0 570 520" aria-label="Open Harbor: It IS Within Reach">
      <text class="title-word" x="124" y="244" font-size="150" textLength="288" lengthAdjust="spacingAndGlyphs">OPEN</text>
      <text class="title-word" x="124" y="372" font-size="135" textLength="288" lengthAdjust="spacingAndGlyphs">HARBOR</text>
      <text class="title-small" x="124" y="412" font-size="30" textLength="58" lengthAdjust="spacingAndGlyphs">IT IS</text>
      <text class="title-small title-struck" x="124" y="446" font-size="28" textLength="66" lengthAdjust="spacingAndGlyphs">IS IT?</text>
      <path class="strike" d="M104 428 L192 448"/>
      <path class="strike" d="M108 450 L190 426"/>
      <text class="title-word" x="192" y="456" font-size="78" textLength="220" lengthAdjust="spacingAndGlyphs">WITHIN REACH</text>
    </svg>

    <p class="cover__tagline">Practical Steps to<br>Move Teams Forward Again</p>

    <div class="cover__artwork" role="img" aria-label="Puzzle pieces coming together, each showing silhouettes of diverse people in groups, with two figures high-fiving at the centre"></div>

    <div class="cover__publisher">
      <span class="publisher-square"></span>
      <span>Lantern Row<br>Publishing</span>
    </div>
  </main>
</body>
</html>
```